LEARN Business Skills so you can Earn a good living

size of the poster is 8”x 10.75" plus 0.25" bleed.
Please leave 1 inch on the bottoum for footer
I want a design a poster that will attract people's attention.
I appreciate a creative ad however the ad should not take away from being able to clearly read the text.
-I also appreciate a simple creative ad that is not too busy.
-you can use graphics, vectors, or pictures of real people.
-however, if you use real people it should be a white male that is wearing a white shirt and look like a professional person.

Target Market(s)

Potential young business people

Industry/Entity Type

education

Requirements
Must have
• easy to read the text
Nice to have
• I would like a "creative" simple ad that is easy to be read
Should not have
• pictures of women

```html
<!DOCTYPE html>
<html lang="en">
<head>
<meta charset="utf-8">
<title>Learn to Earn – Business Enrichment Course</title>
<link href="https://fonts.googleapis.com/css2?family=Oswald:wght@600;700&family=Roboto:ital,wght@0,400;0,500;0,700;1,900&display=swap" rel="stylesheet">
<style>
  :root {
    --taupe: #8c7263;
    --taupe-dark: #6f5a4d;
    --slate: #5b6478;
    --slate-dark: #454c5d;
    --photo-light: #c9ced6;
    --photo-dark: #5e6673;
    --ink: #2f3239;
    --line: #c9b9ae;
    --paper: #ffffff;
  }
  * { box-sizing: border-box; margin: 0; padding: 0; }
  html, body { width: 800px; height: 1200px; overflow: hidden; background: var(--paper); }
  .poster { position: relative; width: 800px; height: 1200px; background: var(--paper); font-family: "Roboto", Arial, sans-serif; color: var(--ink); overflow: hidden; }

  .hero-photo { position: absolute; left: 0; top: 0; width: 800px; height: 440px;
    background: linear-gradient(160deg, var(--photo-light) 0%, #9aa2ae 45%, var(--photo-dark) 100%); }
  .hero-curve { position: absolute; left: 0; top: 330px; width: 800px; height: 140px; }

  .portrait { position: absolute; left: 440px; top: 300px; width: 220px; height: 280px;
    background: linear-gradient(180deg, #e9e7e3 0%, #cfc9c1 60%, #b9b0a6 100%); }

  .headline { position: absolute; left: 60px; top: 425px; font-family: "Oswald", Impact, sans-serif;
    font-weight: 700; font-size: 70px; line-height: 1.02; color: var(--taupe); letter-spacing: 1px; text-transform: uppercase; }

  .course-band { position: absolute; left: 40px; top: 596px; width: 720px; height: 54px; background: var(--slate);
    display: flex; align-items: center; padding-left: 30px; }
  .course-band h2 { font-family: "Roboto", Arial, sans-serif; font-style: italic; font-weight: 900; font-size: 30px; color: #fff; letter-spacing: 0.3px; }

  .benefits { position: absolute; left: 90px; top: 696px; width: 620px; display: flex; justify-content: space-between; }
  .benefit { position: relative; width: 180px; height: 130px; border: 2px solid var(--taupe); border-radius: 6px;
    padding: 34px 12px 10px; text-align: center; font-size: 14px; font-weight: 500; line-height: 1.3; background: #fff; }
  .benefit-icon { position: absolute; left: 50%; top: -24px; width: 46px; height: 46px; margin-left: -23px;
    border-radius: 50%; background: var(--taupe); display: flex; align-items: center; justify-content: center; }

  .subjects { position: absolute; left: 60px; top: 864px; width: 680px; display: flex; flex-wrap: wrap; gap: 8px 8px; justify-content: center; list-style: none; }
  .subject { border: 1px solid var(--line); padding: 5px 10px; font-size: 12.5px; color: var(--ink); background: #fff; }

  .footer-space { position: absolute; left: 0; bottom: 0; width: 800px; height: 120px; background: var(--paper); }
</style>
</head>
<body>
<main class="poster">
  <div class="hero-photo" role="img" aria-label="Photo of hands typing on a laptop with soft glowing learning icons"></div>
  <svg class="hero-curve" viewBox="0 0 800 140" preserveAspectRatio="none" aria-hidden="true">
    <path d="M0 60 C200 140 520 20 800 90 L800 140 L0 140 Z" fill="#ffffff"/>
    <path d="M0 60 C200 140 520 20 800 90" fill="none" stroke="#8c7263" stroke-width="3"/>
  </svg>

  <div class="portrait" role="img" aria-label="Photo of a professional man in a white shirt seated in a chair with a laptop"></div>

  <h1 class="headline">Learn<br>to Earn</h1>

  <div class="course-band"><h2>Business Enrichment Course</h2></div>

  <section class="benefits">
    <div class="benefit">
      <span class="benefit-icon"><svg width="24" height="24" viewBox="0 0 24 24"><path d="M5 12l5 5 9-10" fill="none" stroke="#fff" stroke-width="3"/></svg></span>
      A proven success of helping people in their livelihoods
    </div>
    <div class="benefit">
      <span class="benefit-icon"><svg width="24" height="24" viewBox="0 0 24 24"><rect x="3" y="8" width="18" height="12" rx="2" fill="none" stroke="#fff" stroke-width="2.5"/><path d="M9 8V5h6v3" fill="none" stroke="#fff" stroke-width="2.5"/></svg></span>
      Business skills that will help you
    </div>
    <div class="benefit">
      <span class="benefit-icon"><svg width="24" height="24" viewBox="0 0 24 24"><path d="M4 19l6-6 4 4 6-8" fill="none" stroke="#fff" stroke-width="2.5"/><path d="M15 9h5v5" fill="none" stroke="#fff" stroke-width="2.5"/></svg></span>
      Get a quality set of skills to grow your business &amp; increase your salary
    </div>
  </section>

  <ul class="subjects">
    <li class="subject">Business Administration</li>
    <li class="subject">Small Business Management</li>
    <li class="subject">Information Technology</li>
    <li class="subject">Bookkeeping</li>
    <li class="subject">Finance</li>
    <li class="subject">Accounting</li>
    <li class="subject">Marketing</li>
    <li class="subject">Negotiation</li>
    <li class="subject">Import/Export</li>
    <li class="subject">Public Speaking</li>
    <li class="subject">Entrepreneurship</li>
    <li class="subject">Sales</li>
    <li class="subject">Business Law</li>
    <li class="subject">Real Estate</li>
    <li class="subject">Project Management</li>
    <li class="subject">Leadership</li>
    <li class="subject">Computers</li>
    <li class="subject">Health Care Management</li>
    <li class="subject">Warehousing</li>
    <li class="subject">Banking</li>
    <li class="subject">Analysis</li>
  </ul>

  <footer class="footer-space"></footer>
</main>
</body>
</html>
```